My project benefits Military, First Responders, Police, Fire, and Educators.

Contact Information for Business Card

2 Sided appointment card. Visual side will have my head shot with "Brisk Lantern" in a bold graffic/text. I am picturing maybe the headshot applied to a filter that has a matrix effect where the picture is made up of data/numbers flowing vertically through the photo. I am of course open to other concepts as well. Side two will have contact info presented in an attractive visual complimenting the front.

```html
<!DOCTYPE html>
<html lang="en">
<head>
<meta charset="UTF-8">
<title>Brisk Lantern – Appointment Card</title>
<link rel="stylesheet" href="https://fonts.googleapis.com/css2?family=Source+Sans+3:wght@400;600;700&display=swap">
<style>
  :root {
    --page-bg: #e9e7e4;
    --card-dark: #1e1e20;
    --card-light: #ffffff;
    --brand-blue: #1d63c6;
    --deep-blue: #1a4c9c;
    --text-light: #f2f2f2;
    --dot-line: #333333;
    --photo-top: #6b4a34;
    --photo-bottom: #1d2536;
    --card-shadow: 0 6px 18px rgba(0,0,0,0.18);
  }
  * { box-sizing: border-box; margin: 0; padding: 0; }
  html, body {
    width: 1200px; height: 900px; overflow: hidden;
    background: var(--page-bg);
    font-family: "Source Sans 3", "Myriad Pro", Arial, sans-serif;
  }
  .canvas { position: relative; width: 1200px; height: 900px; }

  .card {
    position: absolute;
    border-radius: 16px;
    overflow: hidden;
    box-shadow: var(--card-shadow);
  }

  /* Front side */
  .card-front {
    left: 78px; top: 35px; width: 588px; height: 364px;
    background: var(--card-dark);
    display: flex;
  }
  .headshot {
    width: 292px; height: 100%;
    background: linear-gradient(160deg, var(--photo-top) 0%, #4a3426 45%, var(--photo-bottom) 100%);
  }
  .identity {
    padding: 122px 0 0 42px;
    color: var(--text-light);
  }
  .identity .person-name {
    color: var(--brand-blue);
    font-size: 21px; font-weight: 600; line-height: 1.15;
  }
  .identity .person-role {
    font-size: 16.5px; line-height: 1.2; margin-bottom: 22px;
  }
  .contact-list { list-style: none; }
  .contact-list li {
    display: flex; align-items: center; gap: 8px;
    font-size: 16.5px; line-height: 21px;
  }
  .contact-list svg { width: 12px; height: 12px; flex: none; fill: var(--brand-blue); }

  /* Back side */
  .card-back {
    left: 390px; top: 507px; width: 564px; height: 349px;
    background: var(--card-light);
    padding: 26px 40px 0 40px;
  }
  .appointment-title {
    color: var(--deep-blue);
    font-size: 20px; font-weight: 700;
  }
  .write-line {
    border-bottom: 2px dotted var(--dot-line);
    height: 0;
  }
  .write-line.first { margin-top: 22px; width: 450px; }
  .write-line.second { margin-top: 46px; width: 460px; }
  .notice {
    margin-top: 26px;
    color: var(--deep-blue);
    font-size: 15.5px; font-weight: 700;
  }
  .brand-mark {
    margin-top: 42px;
    display: flex; align-items: center; justify-content: center; gap: 12px;
    padding-right: 20px;
  }
  .brand-mark .dot {
    width: 20px; height: 20px; border-radius: 50%;
    background: var(--deep-blue);
  }
  .brand-mark .brand-name {
    color: var(--deep-blue);
    font-size: 46px; font-weight: 700; letter-spacing: 0.5px;
  }
</style>
</head>
<body>
<main class="canvas">

  <section class="card card-front" aria-label="Card front">
    <div class="headshot" role="img" aria-label="Headshot photo of the managing director in a suit and tie"></div>
    <div class="identity">
      <p class="person-name">Daniel Carver</p>
      <p class="person-role">Managing Director</p>
      <ul class="contact-list">
        <li>
          <svg viewBox="0 0 24 24" aria-hidden="true"><path d="M6.6 10.8a15.1 15.1 0 0 0 6.6 6.6l2.2-2.2a1 1 0 0 1 1-.25 11.4 11.4 0 0 0 3.6.57 1 1 0 0 1 1 1V20a1 1 0 0 1-1 1A17 17 0 0 1 3 4a1 1 0 0 1 1-1h3.5a1 1 0 0 1 1 1c0 1.25.2 2.46.57 3.6a1 1 0 0 1-.25 1z"/></svg>
          044-555 018 272
        </li>
        <li>
          <svg viewBox="0 0 24 24" aria-hidden="true"><path d="M2 5h20v14H2z M2 5l10 8 10-8" /></svg>
          info@brisklantern.com
        </li>
        <li>
          <svg viewBox="0 0 24 24" aria-hidden="true"><circle cx="12" cy="12" r="10"/></svg>
          www.brisklantern.com
        </li>
      </ul>
    </div>
  </section>

  <section class="card card-back" aria-label="Card back">
    <h2 class="appointment-title">Appointment</h2>
    <div class="write-line first"></div>
    <div class="write-line second"></div>
    <p class="notice">If unable to keep appointment, kindly give 24hrs notice.</p>
    <div class="brand-mark">
      <span class="dot" aria-hidden="true"></span>
      <span class="brand-name">Brisk Lantern</span>
    </div>
  </section>

</main>
</body>
</html>
```